Residential & commercial landscaping company

Updated business cards for commercial and landscaping company. We would like to keep out logo, but just need a more updated business card.

```html
<!DOCTYPE html>
<html lang="en">
<head>
<meta charset="utf-8">
<title>Verdant Ridge Business Cards</title>
<link rel="stylesheet" href="https://fonts.googleapis.com/css2?family=Arimo:wght@400;700&family=Tinos:wght@400;700&display=swap">
<style>
  :root {
    --backdrop: #b8b8b8;
    --card-white: #ffffff;
    --card-black: #000000;
    --brand-green: #0c9b3c;
    --accent-green: #3cc83c;
    --ink-dark: #000000;
    --ink-light: #ffffff;
  }
  * { margin: 0; padding: 0; box-sizing: border-box; }
  html, body {
    width: 1200px; height: 801px; overflow: hidden;
    background: var(--backdrop);
  }
  .sheet { position: relative; width: 1200px; height: 801px; }
  .card {
    position: absolute; left: 379px; width: 443px; height: 264px;
    overflow: hidden;
  }
  .card--front { top: 131px; background: var(--card-black); }
  .card--back { top: 423px; background: var(--card-black); }

  .front__brand-area {
    position: absolute; left: 0; top: 0; width: 100%; height: 151px;
    background: var(--card-white);
  }
  .front__divider {
    position: absolute; left: 0; top: 151px; width: 100%; height: 4px;
    background: var(--brand-green);
  }
  .brand {
    position: absolute; left: 0; width: 100%;
    display: flex; align-items: center; justify-content: center; gap: 10px;
    font-family: "Arimo", sans-serif; font-weight: 700;
    letter-spacing: -0.5px; white-space: nowrap;
  }
  .brand__dot { border-radius: 50%; background: var(--brand-green); flex: none; }
  .brand--front { top: 95px; font-size: 40px; color: var(--ink-dark); }
  .brand--front .brand__dot { width: 16px; height: 16px; }
  .brand--back { top: 95px; font-size: 50px; color: var(--ink-light); }
  .brand--back .brand__dot { width: 20px; height: 20px; }

  .contact {
    position: absolute; left: 0; top: 170px; width: 100%;
    text-align: center; color: var(--ink-light);
  }
  .contact__person {
    font-family: "Tinos", serif; color: var(--accent-green);
    white-space: nowrap; line-height: 22px;
  }
  .contact__name { font-weight: 700; font-size: 18px; }
  .contact__role { font-weight: 400; font-size: 20px; }
  .contact__line {
    font-family: "Arimo", sans-serif; font-size: 13px; line-height: 16px;
    white-space: nowrap;
  }
  .contact__line:first-of-type { margin-top: 7px; }
  .contact__label { color: var(--accent-green); font-weight: 700; }
</style>
</head>
<body>
<main class="sheet">
  <section class="card card--front">
    <div class="front__brand-area">
      <div class="brand brand--front"><span class="brand__dot"></span>Verdant Ridge</div>
    </div>
    <div class="front__divider"></div>
    <div class="contact">
      <p class="contact__person"><span class="contact__name">Daniel Harlow Jr. -</span> <span class="contact__role">Project Manager</span></p>
      <p class="contact__line">555-201-4480 ext.112 | &nbsp;<span class="contact__label">Fax:</span> 555-310-7725</p>
      <p class="contact__line"><span class="contact__label">Email:</span> dan@VerdantRidgeLandscapes.com</p>
    </div>
  </section>

  <section class="card card--back">
    <div class="brand brand--back"><span class="brand__dot"></span>Verdant Ridge</div>
  </section>
</main>
</body>
</html>
```